Web Developer Needs a Business Card Design

I need a personal business card design that represents me as a web developer for potential employers. I would like the background to be a dark color on the front for contrast with my logo and name. The back will have all my information along with a smaller version of the logo. I want something with a modern look and feel, not too conservative. This will be used for potential employers and freelance work.

Industry/Entity Type

Business

Contact Information for Business Card

Front should have my logo and name. The back should have all my personal information which would include: name: Tom Varulek, phone: 570-614-3098, email: tomvarulek@quillbox.net, website url: www.tomvarulek.net, logo, web developer.

Font styles to use
Sans Serif

Requirements
Must have
• Must include my logo. The color palette base color will be the logo color.

```html
<!DOCTYPE html>
<html lang="en">
<head>
<meta charset="utf-8">
<title>Tom Varulek — Business Card</title>
<link rel="stylesheet" href="https://fonts.googleapis.com/css2?family=Roboto:wght@400;500&display=swap">
<style>
  :root {
    --teal: #6cc8b4;
    --teal-light: #b4e3d8;
    --card-black: #0d0d0d;
    --white: #ffffff;
    --page: #e9e6e1;
  }
  * { box-sizing: border-box; margin: 0; padding: 0; }
  html, body { width: 1200px; height: 858px; overflow: hidden; }
  body {
    background: var(--page);
    font-family: "Roboto", Arial, sans-serif;
    position: relative;
  }
  .card {
    position: absolute;
    width: 560px;
    height: 320px;
    background: var(--card-black);
    overflow: hidden;
    box-shadow: 0 10px 24px rgba(0,0,0,.25);
  }
  .card-back { left: 50px; top: 70px; }
  .card-front { left: 590px; top: 468px; }
  .card-bands { position: absolute; inset: 0; width: 100%; height: 100%; }

  .ring {
    position: absolute;
    border: 12px solid var(--teal);
    border-radius: 50%;
  }

  /* back: information side */
  .card-back .ring { left: 58px; top: 92px; width: 136px; height: 136px; }
  .card-back .divider {
    position: absolute; left: 226px; top: 62px;
    width: 2px; height: 196px; background: var(--white);
  }
  .card-back .info { position: absolute; left: 250px; top: 86px; }
  .name {
    color: var(--teal);
    font-weight: 500;
    font-size: 34px;
    line-height: 1;
  }
  .role {
    color: var(--white);
    font-weight: 500;
    font-size: 22px;
    margin-top: 6px;
  }
  .contact {
    list-style: none;
    margin-top: 22px;
    color: var(--white);
    font-size: 15px;
    line-height: 1.55;
  }

  /* front: logo and name */
  .card-front .ring { left: 300px; top: 70px; width: 180px; height: 180px; border-width: 14px; }
  .card-front .name {
    position: absolute; left: 44px; top: 138px;
    font-size: 36px;
  }
</style>
</head>
<body>

<section class="card card-back" aria-label="Card back with contact details">
  <svg class="card-bands" viewBox="0 0 560 320" preserveAspectRatio="none" aria-hidden="true">
    <path d="M0 0 H560 V0 Q280 60 0 0 Z" fill="var(--teal)"/>
    <path d="M0 0 H560 V28 Q280 -8 0 28 Z" fill="var(--teal)"/>
    <path d="M0 28 Q280 -8 560 28 V38 Q280 4 0 38 Z" fill="var(--teal-light)"/>
    <path d="M0 38 Q280 4 560 38 V44 Q280 10 0 44 Z" fill="var(--white)"/>
    <path d="M0 320 H560 V292 Q280 328 0 292 Z" fill="var(--teal)"/>
    <path d="M0 292 Q280 328 560 292 V282 Q280 316 0 282 Z" fill="var(--teal-light)"/>
    <path d="M0 282 Q280 316 560 282 V276 Q280 310 0 276 Z" fill="var(--white)"/>
  </svg>
  <div class="ring" aria-hidden="true"></div>
  <div class="divider" aria-hidden="true"></div>
  <div class="info">
    <h1 class="name">Tom Varulek</h1>
    <p class="role">Web Developer</p>
    <ul class="contact">
      <li>570-614-3098</li>
      <li>tomvarulek@quillbox.net</li>
      <li>www.tomvarulek.net</li>
    </ul>
  </div>
</section>

<section class="card card-front" aria-label="Card front with name">
  <svg class="card-bands" viewBox="0 0 560 320" preserveAspectRatio="none" aria-hidden="true">
    <path d="M0 0 H110 Q60 60 0 70 Z" fill="var(--teal)"/>
    <path d="M560 320 V230 Q520 300 440 320 Z" fill="var(--teal)"/>
  </svg>
  <p class="name">Tom Varulek</p>
  <div class="ring" aria-hidden="true"></div>
</section>

</body>
</html>
```